Moxy Fen needs some awesome stationary

Do you have what it takes to get my brand? You either do or you don't, have a crack at a design and you my just win my business.

I don't want to waste your or my time, so put your creative genius on either a business card or envelope.

I however need a package of stationary that follows the same brand. I will message you to complete the remaining should I like your first submission.

Here is what I need, have a go!

Basically I need the following for my small business based in melbourne.
- Letterhead (printer ready and MS Word)
- Business Card
- Compliments Slip
- Envelope
- Proposal Cover Page (MS Word only)
- Presentation Folder
- Marbled Fox Cards
- Student Name Tent
- Index Cards
- Vell-Ka

I am establishing the brand and it must be modern, professional but also relaxed; that is not formal and not corporate. It represents a company are leaders, but small enough to care and operate like a bunch of friends. We are bringing people and conversations back to business, and turfing out all the bureaucracy and crazy and wasteful procedures. Its about "lets talk and figure it out together and find even better ways".

Target Market(s)

Mainly companies that build software products, but Agile practices are used in many other industries (even graphic design projects)

Industry/Entity Type

Information Technology

Font styles to use
Sans Serif

Colors
3176b5
aaaaaa

Requirements
Must have
• I like curves and circles and not boxes or rectangles.
• I want a colour rich design with my brand colours, but it must be balanced.
• I want more modern than traditional, but simple modern
Should not have
• Not corporate
• Please don't waste my time if your not going to think about it.
• Don't mess with my primary logo
• Don't change my colours
• Don't overlay logo on image

```html
<!DOCTYPE html>
<html lang="en">
<head>
<meta charset="utf-8">
<title>Moxy Fen – Business Card</title>
<link rel="stylesheet" href="https://fonts.googleapis.com/css2?family=Open+Sans:wght@400;600;700&display=swap">
<style>
  :root {
    --brand-blue: #3176b5;
    --brand-blue-deep: #2b5ea8;
    --brand-grey: #aaaaaa;
    --soft-grey: #c4c8cf;
    --mark-blue: #5b7fb8;
    --ink: #4a4f57;
    --muted: #8a8f98;
    --rule: #d9dce1;
    --paper: #ffffff;
    --backdrop: #e9eaec;
  }
  * { box-sizing: border-box; margin: 0; padding: 0; }
  html, body { width: 1200px; height: 950px; overflow: hidden; }
  body {
    background: var(--backdrop);
    font-family: "Open Sans", Arial, sans-serif;
    display: flex;
    flex-direction: column;
    align-items: center;
    justify-content: center;
    gap: 60px;
  }
  .card {
    position: relative;
    width: 700px;
    height: 400px;
    border-radius: 26px;
    overflow: hidden;
    box-shadow: 0 6px 18px rgba(0,0,0,0.18);
  }
  .card--front { background: var(--paper); }
  .card--back { background: var(--brand-blue-deep); }

  .front-swoosh { position: absolute; inset: 0; width: 100%; height: 100%; }

  .brand {
    position: absolute;
    left: 56px;
    top: 116px;
    display: flex;
    align-items: center;
    gap: 18px;
  }
  .brand__dot {
    width: 64px; height: 64px;
    border-radius: 50%;
    background: var(--mark-blue);
  }
  .brand__name {
    font-weight: 700;
    font-size: 48px;
    color: var(--brand-blue);
    letter-spacing: -0.5px;
  }

  .contact {
    position: absolute;
    left: 392px;
    top: 34px;
    padding-left: 24px;
    border-left: 1px solid var(--rule);
  }
  .contact__name {
    font-weight: 700;
    font-size: 21px;
    color: var(--brand-blue);
    line-height: 1.15;
  }
  .contact__role {
    font-size: 13px;
    color: var(--muted);
    margin-bottom: 10px;
  }
  .contact__address {
    font-size: 14px;
    color: var(--ink);
    line-height: 1.35;
    margin-bottom: 8px;
  }
  .contact__list { list-style: none; }
  .contact__item {
    display: flex;
    align-items: center;
    gap: 10px;
    font-size: 14px;
    color: var(--ink);
    line-height: 1.5;
  }
  .contact__icon { width: 13px; height: 13px; fill: var(--brand-blue); flex: none; }

  .back-brand {
    position: absolute;
    right: 70px;
    bottom: 70px;
    display: flex;
    flex-direction: column;
    align-items: flex-end;
    gap: 14px;
  }
  .back-brand__mark { display: flex; align-items: center; gap: 14px; }
  .back-brand__dot {
    width: 46px; height: 46px; border-radius: 50%; background: var(--paper);
  }
  .back-brand__name { font-weight: 700; font-size: 30px; color: var(--paper); }
  .back-brand__url { font-size: 15px; color: var(--paper); letter-spacing: 0.3px; }
</style>
</head>
<body>

  <section class="card card--front" aria-label="Business card front">
    <svg class="front-swoosh" viewBox="0 0 700 400" preserveAspectRatio="none" aria-hidden="true">
      <path d="M0 334 C 250 354, 500 334, 700 266 L 700 400 L 0 400 Z" fill="var(--soft-grey)"/>
      <path d="M0 350 C 250 372, 500 354, 700 290 L 700 400 L 0 400 Z" fill="var(--brand-blue-deep)"/>
    </svg>

    <div class="brand">
      <span class="brand__dot"></span>
      <span class="brand__name">Moxy Fen</span>
    </div>

    <div class="contact">
      <p class="contact__name">Dana Korvell</p>
      <p class="contact__role">CEO, Professional Scrum Trainer</p>
      <p class="contact__address">PO Box 4417<br>Larkfield North<br>VIC 3990, Australia</p>
      <ul class="contact__list">
        <li class="contact__item">
          <svg class="contact__icon" viewBox="0 0 16 16"><path d="M3.5 1.5l2.5 0 1.2 3-1.6 1.2a8 8 0 0 0 4.7 4.7l1.2-1.6 3 1.2v2.5a1.5 1.5 0 0 1-1.6 1.5A12.5 12.5 0 0 1 2 3.1 1.5 1.5 0 0 1 3.5 1.5z"/></svg>
          1300MOXYFEN
        </li>
        <li class="contact__item">
          <svg class="contact__icon" viewBox="0 0 16 16"><path d="M4 1h8a1 1 0 0 1 1 1v12a1 1 0 0 1-1 1H4a1 1 0 0 1-1-1V2a1 1 0 0 1 1-1zm1 2v8h6V3z"/></svg>
          +61 400 172 538
        </li>
        <li class="contact__item">
          <svg class="contact__icon" viewBox="0 0 16 16"><path d="M1 3h14v10H1zm1.5 1.5v.3L8 8.6l5.5-3.8v-.3z"/></svg>
          dana@moxyfen.example
        </li>
        <li class="contact__item">
          <svg class="contact__icon" viewBox="0 0 16 16"><circle cx="8" cy="8" r="7"/></svg>
          www.moxyfen.example
        </li>
      </ul>
    </div>
  </section>

  <section class="card card--back" aria-label="Business card back">
    <div class="back-brand">
      <div class="back-brand__mark">
        <span class="back-brand__dot"></span>
        <span class="back-brand__name">Moxy Fen</span>
      </div>
      <p class="back-brand__url">www.moxyfen.example</p>
    </div>
  </section>

</body>
</html>
```